Lunelle Rosa Hair Fancy Business Card’s

I want my business cards to be elite, original and very classy. I want the business cards to match the colors of my logo and to match the design posted. I would love the design of the picture I posted

I want the card all white .
The dripping on the top of the card I want it to match the pink color in my logo that’s also posted .
I need my logo on the business card !
I need my Instagram- @lunelle.rosa.hair__
And my phone number - 555 207 3962

Target Market(s)

My target market is young woman age 23 to older woman to the age of 65
I want both older and younger women to love my design . I don’t want any cheap looking business cards

Industry/Entity Type

Hair And Beauty

Contact Information for Business Card

Add my logo
Add my Instagram- @lunelle.rosa.hair__
My number - 555 207 3962
My website- www.lunellerosahair.example

Font styles to use
Serif
Script

Colors
ffffff
e667a6
e34298

Requirements
Must have
• The business cards must have my logo, my number , my website, and my Instagram!
Nice to have
• Nice to have glitter words that match my logo
• The business cards must look classy and mature
• I want them to be very unique!!
Should not have
• Should not have any colors that doesn’t match my logo ! This is very important! Please

```html
<!DOCTYPE html>
<html lang="en">
<head>
<meta charset="utf-8">
<title>Lunelle Rosa Hair – Business Cards</title>
<link rel="stylesheet" href="https://fonts.googleapis.com/css2?family=Arvo:wght@400;700&family=Poppins:wght@300;400&display=swap">
<style>
  :root {
    --bg: #ececee;
    --card: #ffffff;
    --frame: #c98ab6;
    --pink: #e34298;
    --pink-soft: #e667a6;
    --grey: #5a5a5c;
    --icon: #b0407e;
  }
  * { margin: 0; padding: 0; box-sizing: border-box; }
  html, body {
    width: 1200px; height: 800px; overflow: hidden;
    background: var(--bg);
  }
  .sheet {
    width: 1200px; height: 800px;
    display: flex; align-items: center; justify-content: center; gap: 40px;
  }
  .card {
    width: 540px; height: 309px;
    background: var(--card);
    border: 14px solid var(--frame);
    position: relative;
    box-shadow: 0 6px 18px rgba(0,0,0,0.12);
  }
  .card-contact {
    display: flex; align-items: center; justify-content: space-between;
    padding: 0 34px 0 48px;
  }
  .identity { text-align: right; }
  .identity-name {
    font-family: "Arvo", serif; font-weight: 700;
    color: var(--pink); font-size: 27px; line-height: 1.1;
  }
  .identity-role {
    font-family: "Arvo", serif; font-weight: 400;
    color: var(--grey); font-size: 20px; margin-top: 2px;
  }
  .contact-list { list-style: none; }
  .contact-item {
    display: flex; align-items: center; gap: 9px;
    font-family: "Poppins", sans-serif; font-weight: 300;
    font-size: 12.5px; color: var(--grey); line-height: 1; margin: 7px 0;
  }
  .contact-icon { width: 15px; height: 15px; flex: none; }
  .card-brand {
    display: flex; align-items: center; justify-content: center;
  }
  .brand-name {
    font-family: "Arvo", serif; font-weight: 700;
    font-size: 38px; color: var(--pink); letter-spacing: 0.5px;
  }
</style>
</head>
<body>
<main class="sheet">
  <section class="card card-contact" aria-label="Business card, contact side">
    <div class="identity">
      <p class="identity-name">Daniel Reyes</p>
      <p class="identity-role">President</p>
    </div>
    <ul class="contact-list">
      <li class="contact-item">
        <svg class="contact-icon" viewBox="0 0 16 16" aria-hidden="true"><rect width="16" height="16" rx="3" fill="var(--icon)"/><path d="M5 4l2 0 1 2.5-1.2 1a6 6 0 0 0 2.7 2.7l1-1.2L13 10v2c-4.5.4-8.4-3.5-8-8z" fill="#fff"/></svg>
        555 207 3962
      </li>
      <li class="contact-item">
        <svg class="contact-icon" viewBox="0 0 16 16" aria-hidden="true"><rect width="16" height="16" rx="3" fill="var(--icon)"/><circle cx="8" cy="8" r="3.6" fill="none" stroke="#fff" stroke-width="1.4"/></svg>
        @lunelle.rosa.hair__
      </li>
      <li class="contact-item">
        <svg class="contact-icon" viewBox="0 0 16 16" aria-hidden="true"><rect width="16" height="16" rx="3" fill="var(--icon)"/><rect x="3.5" y="5" width="9" height="6.5" fill="none" stroke="#fff" stroke-width="1.2"/><path d="M3.5 5l4.5 3.5L12.5 5" fill="none" stroke="#fff" stroke-width="1.2"/></svg>
        info@lunellerosahair.example
      </li>
      <li class="contact-item">
        <svg class="contact-icon" viewBox="0 0 16 16" aria-hidden="true"><rect width="16" height="16" rx="3" fill="var(--icon)"/><circle cx="8" cy="8" r="4.2" fill="none" stroke="#fff" stroke-width="1.2"/><path d="M3.8 8h8.4M8 3.8c-2 2.5-2 5.9 0 8.4M8 3.8c2 2.5 2 5.9 0 8.4" fill="none" stroke="#fff" stroke-width="1"/></svg>
        www.lunellerosahair.example
      </li>
    </ul>
  </section>

  <section class="card card-brand" aria-label="Business card, brand side">
    <p class="brand-name">Lunelle Rosa Hair</p>
  </section>
</main>
</body>
</html>
```